Coastal Learner Bureau business cards

Australian company about to start offering its services. We recruit international students to come to study English, vocational education and postgraduate courses in Australia. We help them find the institution and select the right city they want to come to Australia. We are a young, online oriented and supportive agency. Our clients are between 18 and 35 years old, mainly University students, young professionals or people with work experience. We provide much more information that any other agency offer. We administrate a Facebook group with more than 11.000 members that daily ask questions about general information when coming to Australia, while they are here and even after they leave the country

Target Market(s)

International students from South America, Central America and Europe

Industry/Entity Type

Student

Contact Information for Business Card

Tomas Bilbrea
Managing Director
tomas@kelvarin.com.au
www.kelvoria.com.au
+61 491058264
Melbourne, Australia

Font styles to use
Serif
Sans Serif

Colors

Designer to choose colors to be used in the design.

Requirements
Must have
• Horizontal design
• Standard business card size and shape. If font uses green or yellow colours, they will have to match the ones from the logo
Nice to have
• UPDATE: Use the contents of the green image to design one of the card sides. Use our logo in the background of that side as watermark.
• Passport image, or immigration stamps. A picture of the Yarra River (from Melbourne) would be cool as well.
Should not have
• Non-standard business card size and shape
• Not black as the background colour of any sides as we are not a VIP agency or a hight class service. We are orientes to young people and they like colours, pictures, something attractive.
• Vertical design
• NO YELLOW or BLACK AS THE BACKGROUND COLOUR OF ANY SIDE OF THE BIZ CARD

```html
<!DOCTYPE html>
<html lang="en">
<head>
<meta charset="utf-8">
<title>Coastal Learner Bureau business cards</title>
<link href="https://fonts.googleapis.com/css2?family=Open+Sans:wght@400;600;700&display=swap" rel="stylesheet">
<style>
  :root {
    --canvas-bg: #e9e9e6;
    --green-light: #17804a;
    --green: #0d5e35;
    --green-deep: #08472700;
    --green-dark: #084727;
    --gold-mid: #e6c20c;
    --gold-deep: #d6a50a;
    --card-white: #f6f6f4;
    --text-grey: #5a5a5a;
    --white: #ffffff;
  }
  * { box-sizing: border-box; margin: 0; padding: 0; }
  html, body { width: 1200px; height: 900px; overflow: hidden; }
  body {
    background: var(--canvas-bg);
    font-family: "Open Sans", Arial, sans-serif;
    position: relative;
  }
  .card {
    position: absolute;
    width: 560px;
    height: 320px;
    overflow: hidden;
    box-shadow: 0 8px 24px rgba(0,0,0,0.18);
  }

  /* Front side */
  .card-front {
    left: 130px;
    top: 100px;
    background: linear-gradient(120deg, var(--green-light) 0%, var(--green) 55%, var(--green-dark) 100%);
  }
  .front-brand {
    position: absolute;
    left: 0; right: 0; top: 108px;
    display: flex;
    justify-content: center;
    align-items: center;
    gap: 12px;
    color: var(--white);
    font-weight: 700;
    font-size: 30px;
  }
  .brand-dot {
    width: 16px; height: 16px;
    border-radius: 50%;
    background: var(--white);
  }
  .front-tagline {
    position: absolute;
    left: 0; right: 0; top: 196px;
    display: flex;
    align-items: center;
    justify-content: center;
    gap: 10px;
    color: var(--white);
    font-size: 12px;
    font-weight: 600;
  }
  .tagline-rule { height: 1px; width: 150px; }
  .tagline-rule.left { background: linear-gradient(90deg, rgba(255,255,255,0), rgba(255,255,255,0.8)); }
  .tagline-rule.right { background: linear-gradient(90deg, rgba(255,255,255,0.8), rgba(255,255,255,0)); }

  /* Back side */
  .card-back {
    left: 510px;
    top: 440px;
    background: var(--card-white);
  }
  .back-shapes { position: absolute; inset: 0; }
  .back-brand {
    position: absolute;
    right: 38px;
    top: 44px;
    display: flex;
    align-items: center;
    gap: 8px;
    color: var(--green);
    font-weight: 700;
    font-size: 20px;
  }
  .back-brand .brand-dot { background: var(--green); width: 12px; height: 12px; }
  .contact {
    position: absolute;
    left: 122px;
    top: 184px;
    color: var(--text-grey);
  }
  .contact-name {
    color: var(--green);
    font-weight: 700;
    font-size: 13px;
    line-height: 1.2;
  }
  .contact-role {
    color: var(--gold-deep);
    font-size: 13px;
    line-height: 1.2;
    margin-bottom: 4px;
  }
  .contact-city { font-size: 12px; margin-bottom: 6px; }
  .contact-list { list-style: none; font-size: 12px; }
  .contact-list li {
    display: flex;
    align-items: center;
    gap: 8px;
    line-height: 1.45;
  }
  .contact-list svg { width: 11px; height: 11px; flex: none; }
</style>
</head>
<body>

  <section class="card card-front" aria-label="Card front">
    <div class="front-brand"><span class="brand-dot"></span><span>Coastal Learner Bureau</span></div>
    <div class="front-tagline">
      <span class="tagline-rule left"></span>
      <span>Hacemos más por ti!</span>
      <span class="tagline-rule right"></span>
    </div>
  </section>

  <section class="card card-back" aria-label="Card back">
    <svg class="back-shapes" viewBox="0 0 560 320" preserveAspectRatio="none">
      <path d="M0,100 C60,88 120,82 180,84 C110,120 75,200 62,320 L0,320 Z" fill="var(--green)"/>
      <path d="M170,90 C118,122 88,175 76,240" fill="none" stroke="var(--white)" stroke-width="1.5" opacity="0.8"/>
      <path d="M560,70 C548,190 480,278 372,320 L560,320 Z" fill="var(--gold-mid)"/>
      <path d="M548,150 C530,230 480,282 420,312" fill="none" stroke="var(--white)" stroke-width="2"/>
    </svg>

    <div class="back-brand"><span class="brand-dot"></span><span>Coastal Learner Bureau</span></div>

    <div class="contact">
      <p class="contact-name">TOMAS BILBREA</p>
      <p class="contact-role">MANAGING DIRECTOR</p>
      <p class="contact-city">Melbourne, Australia</p>
      <ul class="contact-list">
        <li>
          <svg viewBox="0 0 12 12" aria-hidden="true"><path d="M2,1 L4.5,1 L5.5,3.5 L4,4.5 C4.7,6 6,7.3 7.5,8 L8.5,6.5 L11,7.5 L11,10 C11,10.6 10.6,11 10,11 C5,11 1,7 1,2 C1,1.4 1.4,1 2,1 Z" fill="var(--text-grey)"/></svg>
          <span>+61 491058264</span>
        </li>
        <li>
          <svg viewBox="0 0 12 12" aria-hidden="true"><rect x="1" y="2.5" width="10" height="7" rx="1" fill="var(--text-grey)"/><path d="M1.5,3 L6,6.5 L10.5,3" fill="none" stroke="var(--card-white)" stroke-width="1"/></svg>
          <span>tomas@kelvarin.com.au</span>
        </li>
        <li>
          <svg viewBox="0 0 12 12" aria-hidden="true"><circle cx="6" cy="6" r="5" fill="var(--text-grey)"/><path d="M1,6 H11 M6,1 C3.5,3.5 3.5,8.5 6,11 M6,1 C8.5,3.5 8.5,8.5 6,11" fill="none" stroke="var(--card-white)" stroke-width="0.8"/></svg>
          <span>www.kelvoria.com.au</span>
        </li>
      </ul>
    </div>
  </section>

</body>
</html>
```